Veltrano.co - Polar Expeditions Specialists

We need a modern, visually striking business card for Veltrano.co, a company specialized in selling expedition cruises to the most remote regions on Earth, with a focus on the Arctic and Antarctica. The design should instantly communicate that the cardholder is an expert in polar travel. Use clean, premium aesthetics with cool tones like icy blue and white, possibly incorporating polar imagery (ice, glaciers, penguins, etc.)

Attached the logo

Contact Information for Business Card

Feels high-end and trustworthy.. Visually memorable — encourages people to keep it

Colors
0054AA
0677BA
7BADD7
CADEEF
E8F1F8

Requirements
Must have
• ice, glaciers, penguins, montains
Nice to have
• modern, transparente,

```html
<!DOCTYPE html>
<html lang="en">
<head>
<meta charset="utf-8">
<title>Veltrano.co Business Card</title>
<link href="https://fonts.googleapis.com/css2?family=Montserrat:wght@400;500;700&family=Poppins:wght@600;700&display=swap" rel="stylesheet">
<style>
  :root {
    --brand-blue: #2f74b8;
    --photo-light: #6a9fd0;
    --photo-mid: #5690c8;
    --photo-deep: #4a82bd;
    --ink: #3c3c3c;
    --paper: #ffffff;
    --backdrop: #eceef0;
  }
  * { margin: 0; padding: 0; box-sizing: border-box; }
  html, body { width: 1192px; height: 1200px; overflow: hidden; background: var(--backdrop); }
  .canvas { position: relative; width: 1192px; height: 1200px; }

  .card {
    position: absolute; left: 219px; width: 754px; height: 430px;
    border-radius: 38px; overflow: hidden;
    box-shadow: 0 14px 28px rgba(0,0,0,0.16);
  }
  .card--front { top: 146px; background: var(--paper); }
  .card--back { top: 623px; }

  .brand { position: absolute; display: flex; align-items: center; gap: 18px; }
  .brand__dot { width: 78px; height: 78px; border-radius: 50%; flex: none; }
  .brand__text { display: flex; flex-direction: column; }
  .brand__name {
    font-family: "Poppins", sans-serif; font-weight: 700; font-size: 64px;
    line-height: 1; letter-spacing: -0.5px;
  }
  .brand__tagline {
    font-family: "Poppins", sans-serif; font-weight: 600; font-size: 18.5px;
    line-height: 1; margin-top: 10px; margin-left: 2px;
  }

  .card--front .brand { left: 150px; top: 74px; color: var(--brand-blue); }
  .card--front .brand__dot { background: var(--brand-blue); }

  .holder {
    position: absolute; right: 401px; top: 236px; text-align: right;
  }
  .holder__name {
    font-family: "Montserrat", sans-serif; font-weight: 700; font-size: 29px;
    color: var(--brand-blue); letter-spacing: 0.5px; line-height: 1.05;
  }
  .holder__role {
    font-family: "Montserrat", sans-serif; font-weight: 400; font-size: 20px;
    color: var(--ink); line-height: 1.2;
  }
  .divider {
    position: absolute; left: 376px; top: 229px; width: 1.5px; height: 70px;
    background: var(--brand-blue);
  }
  .contacts { position: absolute; left: 399px; top: 221px; list-style: none; }
  .contacts li {
    display: flex; align-items: center; gap: 9px; height: 29px;
    font-family: "Montserrat", sans-serif; font-size: 19px; color: var(--ink);
  }
  .contacts svg { width: 14px; height: 14px; fill: var(--brand-blue); flex: none; }
  .address {
    position: absolute; left: 0; right: 0; top: 350px; text-align: center;
    font-family: "Montserrat", sans-serif; font-size: 18.5px; color: var(--ink);
  }

  .polar-photo {
    position: absolute; inset: 0;
    background: radial-gradient(ellipse at 55% 45%, var(--photo-light) 0%, var(--photo-mid) 50%, var(--photo-deep) 100%);
  }
  .card--back .brand { left: 150px; top: 170px; color: var(--paper); }
  .card--back .brand__dot { background: var(--paper); }
</style>
</head>
<body>
<div class="canvas">
  <section class="card card--front">
    <div class="brand">
      <span class="brand__dot"></span>
      <div class="brand__text">
        <span class="brand__name">Veltrano.co</span>
        <span class="brand__tagline">Polar Expeditions Specialists</span>
      </div>
    </div>

    <div class="holder">
      <div class="holder__name">DANIEL MOREAU</div>
      <div class="holder__role">CEO / Founder</div>
    </div>
    <div class="divider"></div>
    <ul class="contacts">
      <li>
        <svg viewBox="0 0 16 16"><path d="M2 6c0-2 3-3 6-3s6 1 6 3v1h-3V5.5C10 5 9 5 8 5s-2 0-3 .5V7H2zM4 8h8l1.5 5h-11z"/></svg>
        +43 600 21 38 745
      </li>
      <li>
        <svg viewBox="0 0 16 16"><path d="M1 6l7-4 7 4v8H1zM2.5 7v.3L8 10.5l5.5-3.2V7L8 3.8z"/></svg>
        daniel.moreau@Veltrano.co
      </li>
      <li>
        <svg viewBox="0 0 16 16"><circle cx="8" cy="8" r="7"/><path d="M5 4c1 1 2 1 2 2s-2 1-2 2 2 1 2 3M10 3c-1 2 1 2 2 3M10 10c1 0 2 1 1 3" stroke="#fff" stroke-width="1.2" fill="none"/></svg>
        www.veltrano.co
      </li>
    </ul>
    <p class="address">P.O. Box 4120 Harbor Lane Nordland AV 6180</p>
  </section>

  <section class="card card--back">
    <div class="polar-photo" role="img" aria-label="Photograph of a polar bear walking on snow, tinted in icy blue"></div>
    <div class="brand">
      <span class="brand__dot"></span>
      <div class="brand__text">
        <span class="brand__name">Veltrano.co</span>
        <span class="brand__tagline">Polar Expeditions Specialists</span>
      </div>
    </div>
  </section>
</div>
</body>
</html>
```